Harborview Estates Business Card for Apartment Buildings

Create business cards for resident managers who run apartment buildings. The audience is the public who are searching for apartment rentals, and current residents who live at the apartment building. Key design element will be incorporating the company logo, however, the logo cannot dominate. The building name and manager name are more important than the logo. Current business card design leaves little room for copy, so we may need to reduce the size on the current card to allow for more space for copy.

Target Market(s)

Adults 18-65 years of age, who are looking for an apartment rental, plus current residents who live at our apartment buildings.

Industry/Entity Type

Property Management

Contact Information for Business Card

A major design element will be use of the company logo. Important property and manager contact information must be part of the design. The size of the logo will need to be reduced to make room for building and manager contact copy.

Font styles to use
Sans Serif

Colors
3176b5
000000
959595
ffffff

Requirements
Must have
• 1) Incorporate the company logo.
• 2) Use the company colors (dark blue, black/grey, over white).
• 3) FEATURE THE BUILDING NAME
• 4) FEATURE THE MANAGER NAME
• 5) The company name is less important than BUILDING and MANAGER
• 6) Manager contact information
• **SEE ATTACHED CREATIVE BRIEF**
Nice to have
• 1) Back of card logo watermark
• 2) Ability to write notes on back of carfd
Should not have
• Avoid letting the company logo dominate the card, the building name and manager are more important than the company logo.

```html
<!DOCTYPE html>
<html lang="en">
<head>
<meta charset="utf-8">
<title>Harborview Estates – Resident Manager Business Card</title>
<link rel="stylesheet" href="https://fonts.googleapis.com/css2?family=Montserrat:wght@600;700&family=Roboto+Condensed:wght@700&family=Roboto:wght@400&display=swap">
<style>
  :root {
    --brand-blue: #1f68a4;
    --ink-grey: #3f3f3f;
    --text-grey: #4a4a4a;
    --card-white: #f3f3f3;
    --backdrop: #2b2b2b;
  }
  * { margin: 0; padding: 0; box-sizing: border-box; }
  html, body { width: 1200px; height: 960px; overflow: hidden; }
  body {
    background: var(--backdrop);
    position: relative;
    font-family: "Roboto", Arial, sans-serif;
  }
  .card {
    position: absolute;
    width: 600px;
    height: 342px;
    background: var(--card-white);
    overflow: hidden;
  }
  .card-front { left: 314px; top: 113px; }
  .card-back  { left: 311px; top: 472px; }

  .accent-circle {
    position: absolute;
    left: 298px;
    top: 34px;
    width: 316px;
    height: 316px;
    border-radius: 50%;
    background: var(--brand-blue);
  }

  .manager-name {
    position: absolute;
    left: 43px;
    top: 49px;
    font-family: "Montserrat", Arial, sans-serif;
    font-weight: 700;
    font-size: 21px;
    letter-spacing: 0.3px;
    color: var(--brand-blue);
    text-transform: uppercase;
  }
  .manager-title {
    position: absolute;
    left: 43px;
    top: 74px;
    font-family: "Montserrat", Arial, sans-serif;
    font-weight: 600;
    font-size: 14px;
    letter-spacing: 0.6px;
    color: var(--ink-grey);
    text-transform: uppercase;
  }
  .building-name {
    position: absolute;
    left: 43px;
    top: 130px;
    font-family: "Roboto Condensed", Arial, sans-serif;
    font-weight: 700;
    font-size: 22px;
    color: var(--brand-blue);
  }
  .building-address {
    position: absolute;
    left: 43px;
    top: 156px;
    font-size: 14px;
    line-height: 19px;
    color: var(--text-grey);
    font-style: normal;
  }
  .contact-list {
    position: absolute;
    left: 43px;
    top: 210px;
    list-style: none;
  }
  .contact-item {
    display: flex;
    align-items: center;
    height: 19px;
    font-size: 14px;
    color: var(--text-grey);
  }
  .contact-icon {
    width: 13px;
    height: 13px;
    margin-right: 10px;
    fill: var(--brand-blue);
    flex: none;
  }

  .company-lockup {
    position: absolute;
    left: 0;
    right: 0;
    top: 150px;
    display: flex;
    justify-content: center;
    align-items: center;
  }
  .company-marker {
    width: 30px;
    height: 30px;
    background: var(--brand-blue);
    margin-right: 12px;
  }
  .company-name {
    font-family: "Roboto Condensed", Arial, sans-serif;
    font-weight: 700;
    font-size: 34px;
    letter-spacing: 1px;
    color: var(--brand-blue);
    text-transform: uppercase;
  }
</style>
</head>
<body>

<section class="card card-front" aria-label="Card front">
  <div class="accent-circle"></div>

  <h1 class="manager-name">Marisol Delgado</h1>
  <p class="manager-title">Resident Manager</p>

  <h2 class="building-name">Bayside Court Apartments</h2>
  <address class="building-address">2845 Cedar Lane<br>Fairhaven, CA 90000</address>

  <ul class="contact-list">
    <li class="contact-item">
      <svg class="contact-icon" viewBox="0 0 16 16" aria-hidden="true"><path d="M3.6 1.2l2.3 2.6-1.3 2.1c.9 2 2.5 3.6 4.5 4.5l2.1-1.3 2.6 2.3-1.3 2.4C7 13.5 2.5 9 1.2 2.5z"/></svg>
      555-210-4471
    </li>
    <li class="contact-item">
      <svg class="contact-icon" viewBox="0 0 16 16" aria-hidden="true"><path d="M4 1h8v14H4zM5.5 2.5v9h5v-9zM7.2 12.6h1.6v1.2H7.2z" fill-rule="evenodd"/></svg>
      555-318-6042
    </li>
    <li class="contact-item">
      <svg class="contact-icon" viewBox="0 0 16 16" aria-hidden="true"><path d="M4 1h8v4H4zM1 6h14v6h-2v3H3v-3H1zM4.5 10v3.5h7V10z" fill-rule="evenodd"/></svg>
      555-406-9130
    </li>
    <li class="contact-item">
      <svg class="contact-icon" viewBox="0 0 16 16" aria-hidden="true"><path d="M1 3h14v10H1zM2.5 4.5L8 8.6l5.5-4.1z" fill-rule="evenodd"/></svg>
      marisol@harborview.com
    </li>
    <li class="contact-item">
      <svg class="contact-icon" viewBox="0 0 16 16" aria-hidden="true"><circle cx="8" cy="8" r="7"/><path d="M3 8h10M8 1.5c2.2 2 2.2 11 0 13M8 1.5c-2.2 2-2.2 11 0 13" stroke="#f3f3f3" stroke-width="1.1" fill="none"/></svg>
      www.harborview.com
    </li>
  </ul>
</section>

<section class="card card-back" aria-label="Card back">
  <div class="company-lockup">
    <span class="company-marker" aria-hidden="true"></span>
    <span class="company-name">Harborview Estates LLC</span>
  </div>
</section>

</body>
</html>
```